Human Resource Consulting practice needs a business card design

We need a business card design (double sided colour) for our Human Resource (HR) consulting practice in regional New South Wales, australia. Our business name is Staff Compass. We support small and medium business across the Mid North Coast of New South Wales by providing them with outsourced HR support, services and products to help them achieve compliance with workplace legislation and across all areas of the employment lifecycle from recruitment to termination and everything in between. Our corporate colours are hot pink and black. The final design should communicate professionalism, trust, people focus.
I have attached the current (old) business card for your reference.

Target Market(s)

Business owners and high level managers

Industry/Entity Type

Business

Contact Information for Business Card

Name
Title
Phone no
Mobile no
Address
PO Box
email address
website

Colors
e34197

Requirements
Must have
• Tempate for changing business card personal details including Name, position title, mobile number, email address.
• Keep current logo and colours as per attached
• Logo must be presented in 2 colours or black only not white
Nice to have
• One side logo and graphic only other side logo and personal details
Should not have
• Should not be the same as the current version (attached) but a modern interpretation.
• Does not need a busy reverse side with our list of services as per current version. I feel this is too busy.
• No photos

```html
<!DOCTYPE html>
<html lang="en">
<head>
<meta charset="utf-8">
<title>Staff Compass – Business Card</title>
<link href="https://fonts.googleapis.com/css2?family=Michroma&display=swap" rel="stylesheet">
<style>
  :root {
    --stage: #e9e7e4;
    --card-white: #ffffff;
    --card-grey: #ececec;
    --ink: #2f2f31;
    --charcoal: #3a3a3c;
    --pink: #e6177f;
    --on-dark: #ffffff;
    --on-dark-soft: #cfcfd2;
  }
  * { margin: 0; padding: 0; box-sizing: border-box; }
  html, body { width: 1200px; height: 828px; overflow: hidden; }
  body {
    background: var(--stage);
    font-family: "Michroma", sans-serif;
    position: relative;
  }
  .card {
    position: absolute;
    width: 540px;
    height: 309px;
    overflow: hidden;
    background: radial-gradient(ellipse at 50% 40%, var(--card-white) 0%, var(--card-grey) 100%);
    box-shadow: 0 6px 18px rgba(0,0,0,0.18);
  }
  .card--front { left: 40px; top: 260px; }
  .card--back { left: 620px; top: 260px; }

  .logo {
    position: absolute;
    display: flex;
    align-items: center;
    gap: 10px;
    color: var(--ink);
    font-size: 26px;
    letter-spacing: 0.5px;
    white-space: nowrap;
  }
  .logo__dot {
    width: 14px; height: 14px;
    border-radius: 50%;
    background: var(--pink);
  }
  .card--front .logo { left: 50%; top: 50%; transform: translate(-50%, -50%); }
  .card--back .logo { left: 96px; top: 72px; font-size: 22px; }

  .back-shape { position: absolute; inset: 0; }

  .holder {
    position: absolute;
    left: 48px;
    bottom: 40px;
    color: var(--on-dark);
  }
  .holder__name { font-size: 11px; letter-spacing: 1px; text-transform: uppercase; }
  .holder__title { font-size: 8px; letter-spacing: 1px; color: var(--on-dark-soft); text-transform: uppercase; margin-top: 4px; }

  .contact {
    position: absolute;
    color: var(--on-dark);
    font-size: 7.5px;
    line-height: 1.9;
    letter-spacing: 0.3px;
  }
  .contact--address { left: 262px; top: 192px; }
  .contact--online { left: 395px; top: 158px; }
  .contact__row { display: flex; align-items: center; gap: 6px; white-space: nowrap; }
  .contact__icon { width: 9px; height: 9px; fill: var(--on-dark); flex: none; }
  .contact__spacer { height: 8px; }
</style>
</head>
<body>

  <section class="card card--front" aria-label="Card front">
    <div class="logo"><span class="logo__dot"></span><span class="logo__name">Staff Compass</span></div>
  </section>

  <section class="card card--back" aria-label="Card back">
    <svg class="back-shape" viewBox="0 0 540 309" preserveAspectRatio="none">
      <path d="M0,208 Q300,196 540,36 L540,309 L0,309 Z" fill="var(--pink)"/>
      <path d="M0,218 Q305,206 540,50 L540,309 L0,309 Z" fill="var(--charcoal)"/>
    </svg>

    <div class="logo"><span class="logo__dot"></span><span class="logo__name">Staff Compass</span></div>

    <div class="contact contact--address">
      <div>12 Harbour Lane</div>
      <div>Port Kelso NSW</div>
      <div class="contact__spacer"></div>
      <div class="contact__row">
        <svg class="contact__icon" viewBox="0 0 10 10"><path d="M2 0.5 L4 2.5 L3 4 Q4.5 6 6 7 L7.5 6 L9.5 8 L8 9.5 Q3 9 0.5 2 Z"/></svg>
        <span>02 6500 1234</span>
      </div>
      <div class="contact__row">
        <svg class="contact__icon" viewBox="0 0 10 10"><rect x="2.5" y="0.5" width="5" height="9" rx="1"/></svg>
        <span>0400 555 210</span>
      </div>
    </div>

    <div class="contact contact--online">
      <div class="contact__row">
        <svg class="contact__icon" viewBox="0 0 10 10"><path d="M0.5 2 H9.5 V8 H0.5 Z M0.5 2 L5 5.5 L9.5 2" fill="none" stroke="var(--on-dark)" stroke-width="1"/></svg>
        <span>hello@staffcompass.au</span>
      </div>
      <div class="contact__row">
        <svg class="contact__icon" viewBox="0 0 10 10"><circle cx="5" cy="5" r="4.2" fill="none" stroke="var(--on-dark)" stroke-width="1"/><path d="M1 5 H9 M5 1 V9" stroke="var(--on-dark)" stroke-width="0.8"/></svg>
        <span>www.staffcompass.au</span>
      </div>
    </div>

    <div class="holder">
      <div class="holder__name">Dana Holloway</div>
      <div class="holder__title">President</div>
    </div>
  </section>

</body>
</html>
```